Kestrel Baseball & Softball Camp 2017

Design a flyer that will promote our 2017 summer camp for boys and girls softball.

Weeks of
July 10th - 14th
July 17th - 21st.

Players ages 5 - 11.
Full day = 9:30am - 2:30pm half day = 9:30am - 11:30am.
$295 / full day : $195/ half day

Hosted by "Kestrel Baseball" affiliated with the Harbor Comets Travel Baseball & Softball Club and the Maple Ridge Youth League,

Camp Location MRYL, Route 9C Birch Hollow.

PHone 555-240-7813, email info@kestrelball.example

The color should be "Red white and blue color scheme" with dates and location standing out. Kestrel Logo should be prominent MRYL and Comets smaller and secondary.

Feel free to use stock photo's if available. visit www.harborcomets.example for more pictures and there are links for the 2017 summer camp there with possibly some more information.

Target Market(s)

to catch the eye of parents of players ages 5 - 11 already at little league or shopping in local stores

Colors
ec1f27
0355a3
ffffff

Requirements
Must have
• red white and blue design,
• Kestrel logo and summer camp prominent so it catches the eye and explains what it is right away.
• the comets and maple ridge logo's a the bottom showing the affiliation.
Nice to have
• stock photo's or something showing players having a great time or a beautiful ballpark
Should not have
• to much clutter or hard to figure out what it's for

```html
<!DOCTYPE html>
<html lang="en">
<head>
<meta charset="utf-8">
<title>Kestrel Softball Summer Camp 2017</title>
<link rel="stylesheet" href="https://fonts.googleapis.com/css2?family=Bebas+Neue&family=Oswald:wght@400;500;700&family=Yellowtail&display=swap">
<style>
  :root {
    --red: #ec1f27;
    --blue: #0355a3;
    --navy: #1d2f6b;
    --white: #ffffff;
    --ink: #1a1a1a;
  }
  * { margin: 0; padding: 0; box-sizing: border-box; }
  html, body { width: 820px; height: 1200px; overflow: hidden; background: var(--white); }
  .flyer { position: relative; width: 820px; height: 1200px; overflow: hidden; background: var(--white); font-family: "Oswald", sans-serif; color: var(--white); }

  .hero-photo {
    position: absolute; left: 0; top: 0; width: 600px; height: 420px;
    background: radial-gradient(ellipse at 55% 45%, #f1c9ab 0%, #d99a74 35%, #b06a45 60%, #f4f4f4 85%);
  }
  .waves { position: absolute; left: 0; top: 0; width: 820px; height: 1200px; }

  .brand-badge {
    position: absolute; left: 470px; top: 255px; width: 200px; height: 200px;
    border-radius: 50%; background: var(--white);
    display: flex; align-items: center; justify-content: center;
    box-shadow: 0 2px 6px rgba(0,0,0,.15);
  }
  .brand-name { font-family: "Bebas Neue", sans-serif; font-size: 50px; color: var(--red); letter-spacing: 1px; }

  .headline { position: absolute; left: 56px; top: 470px; }
  .headline-script { font-family: "Yellowtail", cursive; color: var(--red); font-size: 56px; line-height: .9; height: 50px; margin-left: 60px; white-space: nowrap; }
  .headline-main { font-family: "Bebas Neue", sans-serif; font-weight: 400; font-size: 140px; line-height: .85; letter-spacing: 1px; white-space: nowrap; }
  .headline-main .summer { color: var(--red); }
  .headline-main .camp { color: var(--navy); }
  .headline-year {
    position: absolute; left: 620px; top: 170px; transform-origin: left top; transform: rotate(-90deg);
    font-family: "Bebas Neue", sans-serif; font-size: 64px; line-height: 1; color: var(--red); letter-spacing: 2px;
  }
  .headline-audience { font-family: "Yellowtail", cursive; color: var(--navy); font-size: 30px; margin: 2px 0 0 424px; line-height: 1; white-space: nowrap; }

  .hosted-by { position: absolute; left: 56px; top: 690px; width: 560px; font-size: 12px; font-weight: 700; color: var(--ink); text-transform: uppercase; line-height: 1.9; letter-spacing: .2px; }
  .partner-badge { position: absolute; left: 268px; top: 735px; width: 56px; height: 56px; border-radius: 50%; background: #e9f3e2; border: 2px solid #7fb241; }

  .ages { position: absolute; left: 505px; top: 830px; display: flex; align-items: center; gap: 12px; }
  .ages-label { font-weight: 700; font-size: 26px; line-height: 1.05; text-transform: uppercase; }
  .ages-value { margin-left: 20px; width: 104px; height: 104px; border-radius: 50%; background: var(--navy); display: flex; align-items: center; justify-content: center; font-weight: 700; font-size: 32px; white-space: nowrap; }

  .details { position: absolute; left: 56px; top: 938px; width: 730px; display: flex; }
  .detail { padding: 0 20px; border-left: 2px solid var(--white); }
  .detail:first-child { border-left: none; padding-left: 0; }
  .detail-hours { width: 232px; display: flex; gap: 12px; }
  .detail-weeks { width: 258px; }
  .detail-cost { flex: 1; padding-right: 0; }
  .label-bold { font-weight: 700; font-size: 20px; line-height: 1.3; text-transform: uppercase; white-space: nowrap; }
  .label-script { font-family: "Yellowtail", cursive; font-size: 26px; line-height: 1; height: 30px; margin-bottom: 4px; white-space: nowrap; }
  .week { font-weight: 700; font-size: 28px; line-height: 1.3; text-transform: uppercase; white-space: nowrap; }
  .week::before { content: "▸ "; font-size: 18px; vertical-align: middle; }
  .cost { display: flex; gap: 10px; align-items: center; }
  .cost-lines { font-weight: 700; font-size: 20px; line-height: 1.35; text-transform: uppercase; white-space: nowrap; }

  .divider { position: absolute; left: 56px; top: 1090px; width: 730px; border-top: 3px dashed var(--white); }

  .footer { position: absolute; left: 56px; top: 1106px; width: 740px; display: flex; align-items: flex-start; }
  .cta { font-family: "Yellowtail", cursive; font-size: 38px; line-height: 1.1; width: 250px; margin-top: 16px; white-space: nowrap; }
  .footer-item { display: flex; gap: 8px; }
  .footer-location { width: 210px; }
  .footer-title { font-family: "Yellowtail", cursive; font-size: 22px; line-height: 1.1; white-space: nowrap; }
  .footer-text { font-weight: 500; font-size: 14px; line-height: 1.4; text-transform: uppercase; white-space: nowrap; }
  .footer-contact .footer-text { text-transform: none; }
  .icon { flex: none; }
</style>
</head>
<body>
<main class="flyer">
  <div class="hero-photo" role="img" aria-label="Smiling young softball player in a backwards cap holding a bat and a glove with a ball"></div>

  <svg class="waves" viewBox="0 0 820 1200" aria-hidden="true">
    <path d="M0 330 C200 410 420 410 820 250 L820 300 C440 450 200 440 0 380 Z" fill="var(--navy)"/>
    <path d="M0 372 C220 440 440 440 820 300 L820 335 C450 480 220 470 0 412 Z" fill="var(--red)"/>
    <path d="M0 785 C250 715 520 735 820 870 L820 890 C520 775 260 765 0 815 Z" fill="var(--navy)"/>
    <path d="M0 828 C260 780 520 805 820 910 L820 1200 L0 1200 Z" fill="var(--red)"/>
  </svg>

  <div class="brand-badge"><span class="brand-name">Kestrel</span></div>

  <section class="headline">
    <p class="headline-script">Softball</p>
    <h1 class="headline-main"><span class="summer">SUMMER</span><span class="camp">CAMP</span></h1>
    <span class="headline-year">2017</span>
    <p class="headline-audience">for boys and girls</p>
  </section>

  <p class="hosted-by">Hosted by "Kestrel Baseball" affiliated with the Harbor Comets Travel<br>Baseball &amp; Softball Club and the Maple Ridge Youth League</p>
  <div class="partner-badge" role="img" aria-label="Maple Ridge Youth League badge"></div>

  <div class="ages">
    <svg class="icon" width="34" height="34" viewBox="0 0 34 34" aria-hidden="true"><circle cx="10" cy="6" r="4" fill="var(--navy)"/><rect x="6" y="12" width="8" height="20" rx="2" fill="var(--navy)"/><circle cx="24" cy="6" r="4" fill="var(--navy)"/><rect x="20" y="12" width="8" height="20" rx="2" fill="var(--navy)"/></svg>
    <p class="ages-label">Players<br>Ages</p>
    <p class="ages-value">5 - 11</p>
  </div>

  <section class="details">
    <div class="detail detail-hours">
      <svg class="icon" width="28" height="28" viewBox="0 0 30 30" aria-hidden="true"><circle cx="15" cy="16" r="11" fill="none" stroke="var(--white)" stroke-width="3.5"/><path d="M15 10 V16 H20" stroke="var(--white)" stroke-width="3" fill="none"/><rect x="11" y="1" width="8" height="3" fill="var(--white)"/></svg>
      <div>
        <p class="label-bold">Full Day</p>
        <p class="label-bold">9:30AM - 2:30PM</p>
        <p class="label-bold">Half Day</p>
        <p class="label-bold">9:30AM - 11:30AM</p>
      </div>
    </div>
    <div class="detail detail-weeks">
      <p class="label-script">Weeks of</p>
      <p class="week">July 10th - 14th</p>
      <p class="week">July 17th - 21st.</p>
    </div>
    <div class="detail detail-cost">
      <p class="label-script">Cost:</p>
      <div class="cost">
        <svg class="icon" width="32" height="32" viewBox="0 0 34 34" aria-hidden="true"><circle cx="17" cy="17" r="16" fill="var(--white)"/><text x="17" y="25" text-anchor="middle" font-family="Oswald, sans-serif" font-weight="700" font-size="22" fill="var(--red)">$</text></svg>
        <p class="cost-lines">$295 / Full Day<br>$195/ Half Day</p>
      </div>
    </div>
  </section>

  <div class="divider"></div>

  <footer class="footer">
    <p class="cta">Register today!</p>
    <div class="footer-item footer-location">
      <svg class="icon" width="20" height="26" viewBox="0 0 20 26" aria-hidden="true"><path d="M10 0 C4 0 0 4 0 10 C0 17 10 26 10 26 C10 26 20 17 20 10 C20 4 16 0 10 0 Z" fill="var(--navy)"/><circle cx="10" cy="10" r="4" fill="var(--red)"/></svg>
      <div>
        <p class="footer-title">Camp Location:</p>
        <p class="footer-text">MRYL, Route 9C<br>Birch Hollow.</p>
      </div>
    </div>
    <div class="footer-item footer-contact">
      <svg class="icon" width="18" height="28" viewBox="0 0 18 28" aria-hidden="true"><rect x="1" y="1" width="16" height="26" rx="3" fill="var(--navy)"/><rect x="4" y="5" width="10" height="15" fill="var(--red)"/><circle cx="9" cy="23.5" r="1.6" fill="var(--white)"/></svg>
      <div>
        <p class="footer-title">Contact:</p>
        <p class="footer-text">PHONE 555-240-7813<br>EMAIL info@kestrelball.example</p>
      </div>
    </div>
  </footer>
</main>
</body>
</html>
```